Brightfen Business Card Redesign & Logo Update

We need to update our business cards to something more modern and fresh. Brightfen can provide the current color schemes and old design examples, but welcome creativity in helping us with this redesign. PLEASE NOTE that we no longer utilize the "tree" and/or "leaf" imagery in our branding. If able would apprecaite an update on the quality of our "words only" logo in Ai. / PNG formats too.

Target Market(s)

Investors, landowners, corporate partners, contractors

Industry/Entity Type

Environmental Restoration & Conservation

Contact Information for Business Card

Logo, persons name, title, mailing address, phone and email, website url

Font styles to use
Other font styles liked:
• Merriweather

Requirements
Nice to have
• Logo, persons name, title, mailing address, phone and email, website url, but open to ideams
Should not have
• No all back backgrounds

```html
<!DOCTYPE html>
<html lang="en">
<head>
<meta charset="utf-8">
<title>Brightfen Business Card</title>
<link rel="stylesheet" href="https://fonts.googleapis.com/css2?family=Oswald:wght@500;700&family=Roboto:wght@400&display=swap">
<style>
  :root {
    --bg: #c9c9c9;
    --green: #117f35;
    --orange: #ef7d00;
    --ink: #1b1b1b;
    --text: #2a2a2a;
    --paper: #ffffff;
    --ghost-light: #ececec;
    --ghost-dark: rgba(60,50,0,0.18);
  }
  * { margin: 0; padding: 0; box-sizing: border-box; }
  html, body { width: 1200px; height: 900px; overflow: hidden; }
  body {
    background: var(--bg);
    position: relative;
    font-family: "Roboto", sans-serif;
  }
  .card {
    position: absolute;
    left: 270px;
    width: 660px;
    height: 378px;
    border-radius: 30px;
    overflow: hidden;
    box-shadow: 0 6px 14px rgba(0,0,0,0.25);
  }
  .card--front {
    top: 48px;
    background: linear-gradient(to bottom, var(--green) 0%, #6e7a22 42%, #c47c0e 70%, var(--orange) 100%);
  }
  .card--back {
    top: 474px;
    background: var(--paper);
  }
  .wordmark, .ghost-name {
    font-family: "Oswald", sans-serif;
    font-weight: 700;
    text-transform: uppercase;
    line-height: 1;
    letter-spacing: 1px;
    white-space: nowrap;
  }
  .tagline {
    font-family: "Oswald", sans-serif;
    font-weight: 500;
    text-transform: uppercase;
    line-height: 1;
    letter-spacing: 0.3px;
    white-space: nowrap;
  }
  .ghost-name { position: absolute; }

  /* Front */
  .front-logo {
    position: absolute;
    left: 110px;
    top: 96px;
    color: var(--paper);
  }
  .front-logo .wordmark { font-size: 80px; }
  .front-logo .tagline { font-size: 19px; margin-top: 6px; padding-left: 3px; }
  .card--front .ghost-name {
    left: 380px;
    top: 226px;
    font-size: 56px;
    color: var(--ghost-dark);
  }

  /* Back */
  .back-logo {
    position: absolute;
    left: 44px;
    top: 60px;
  }
  .back-logo .wordmark { font-size: 58px; color: var(--green); }
  .back-logo .tagline { font-size: 17px; color: var(--ink); margin-top: 5px; padding-left: 2px; }
  .card--back .ghost-name {
    left: 372px;
    top: 96px;
    font-size: 56px;
    color: var(--ghost-light);
  }
  .person {
    position: absolute;
    left: 48px;
    top: 196px;
  }
  .person-name {
    font-family: "Oswald", sans-serif;
    font-weight: 500;
    font-size: 34px;
    text-transform: uppercase;
    line-height: 1.05;
  }
  .person-name .first { color: var(--orange); }
  .person-name .last { color: var(--green); }
  .person-title { font-size: 19px; color: var(--text); margin-top: 2px; }
  .contact-list {
    list-style: none;
    margin-top: 12px;
  }
  .contact-list li {
    display: flex;
    align-items: center;
    gap: 10px;
    font-size: 17px;
    color: var(--text);
    height: 26px;
  }
  .contact-list svg { width: 17px; height: 17px; flex: none; }
  .address {
    position: absolute;
    right: 40px;
    bottom: 52px;
    text-align: right;
    font-size: 17px;
    line-height: 1.4;
    color: var(--text);
    font-style: normal;
  }
</style>
</head>
<body>

<section class="card card--front" aria-label="Business card front">
  <div class="ghost-name" aria-hidden="true">Brightfen</div>
  <div class="front-logo">
    <div class="wordmark">Brightfen</div>
    <div class="tagline">Environmental Credit Company</div>
  </div>
</section>

<section class="card card--back" aria-label="Business card back">
  <div class="ghost-name" aria-hidden="true">Brightfen</div>
  <div class="back-logo">
    <div class="wordmark">Brightfen</div>
    <div class="tagline">Environmental Credit Company</div>
  </div>

  <div class="person">
    <div class="person-name"><span class="first">Daniel</span> <span class="last">Harper</span></div>
    <div class="person-title">Managing Director</div>
    <ul class="contact-list">
      <li>
        <svg viewBox="0 0 24 24" aria-hidden="true"><path fill="var(--orange)" d="M6.6 10.8a15.1 15.1 0 0 0 6.6 6.6l2.2-2.2a1 1 0 0 1 1-.25 11.4 11.4 0 0 0 3.6.57 1 1 0 0 1 1 1V20a1 1 0 0 1-1 1A17 17 0 0 1 3 4a1 1 0 0 1 1-1h3.5a1 1 0 0 1 1 1c0 1.25.2 2.45.57 3.57a1 1 0 0 1-.25 1z"/></svg>
        044-555 210 347
      </li>
      <li>
        <svg viewBox="0 0 24 24" aria-hidden="true"><rect x="2" y="5" width="20" height="14" rx="1" fill="var(--orange)"/><path d="M3 6l9 7 9-7" fill="none" stroke="#fff" stroke-width="1.6"/></svg>
        hello@brightfen-mail.com
      </li>
      <li>
        <svg viewBox="0 0 24 24" aria-hidden="true"><g fill="none" stroke="var(--orange)" stroke-width="2"><circle cx="12" cy="12" r="9"/><ellipse cx="12" cy="12" rx="4" ry="9"/><path d="M3 12h18M5 7h14M5 17h14"/></g></svg>
        www.brightfen-site.com
      </li>
    </ul>
  </div>

  <address class="address">
    421, Address line goes here<br>
    45452,Country Name
  </address>
</section>

</body>
</html>
```